BOLD & MINIMALIST DESIGN NEEDED

We want a very bold but minimalistic business card design that is impactful and utilizes both sides of the business card. Our current logo is included for your use.

We want bold fonts and good use of negative space. We don't want the logo to overpower the design.

Target Market(s)

Professionals who are building new commercial buildings.

Industry/Entity Type

Construction

Contact Information for Business Card

Name, Title, email, office phone, cell phone, website

Font styles to use
Serif
Sans Serif

Requirements
Must have
• Bold design!

```html
<!DOCTYPE html>
<html lang="en">
<head>
<meta charset="utf-8">
<title>Ridgeline Design + Build — Business Card</title>
<link href="https://fonts.googleapis.com/css2?family=Arimo:wght@400;700&display=swap" rel="stylesheet">
<style>
  :root {
    --page: #e4e4e4;
    --card-light: #ffffff;
    --card-dark: #2f2f2f;
    --ink: #111111;
    --text-grey: #555555;
    --green: #7dc242;
    --green-light: #c4e59a;
    --white: #ffffff;
  }
  * { margin: 0; padding: 0; box-sizing: border-box; }
  html, body {
    width: 1200px; height: 1200px; overflow: hidden;
    background: var(--page);
    font-family: "Arimo", Arial, sans-serif;
  }
  .card {
    position: absolute;
    width: 688px; height: 393px;
    box-shadow: 0 18px 30px rgba(0,0,0,0.18);
    overflow: hidden;
  }
  .card--front { left: 267px; top: 159px; background: var(--card-light); }
  .card--back  { left: 262px; top: 653px; background: var(--card-dark); }

  .brand {
    position: absolute; left: 112px; top: 168px;
    display: flex; align-items: center; gap: 10px;
  }
  .brand__mark { width: 14px; height: 14px; background: var(--green); }
  .brand__name {
    font-weight: 700; font-size: 34px; color: var(--ink); letter-spacing: 1px;
  }

  .divider {
    position: absolute; left: 360px; top: 110px;
    width: 2px; height: 156px;
    background: linear-gradient(to bottom, rgba(0,0,0,0), #cfcfcf 20%, #cfcfcf 80%, rgba(0,0,0,0));
  }

  .person { position: absolute; left: 387px; top: 122px; }
  .person__name { font-weight: 700; font-size: 27px; color: var(--ink); letter-spacing: 0.5px; }
  .person__title { font-size: 16px; color: var(--green); margin-top: 3px; }

  .contacts { position: absolute; left: 387px; top: 190px; list-style: none; }
  .contacts li {
    display: flex; align-items: center; gap: 11px;
    font-size: 16px; color: var(--text-grey); height: 21px;
  }
  .contacts svg { width: 14px; height: 14px; fill: var(--ink); }

  .footer-band { position: absolute; left: 0; bottom: 0; width: 688px; height: 31px; }
  .footer-band__url {
    position: absolute; right: 44px; bottom: 6px;
    font-size: 16px; color: var(--white);
  }

  .back-brand {
    position: absolute; left: 0; right: 0; top: 150px;
    display: flex; justify-content: center; align-items: center; gap: 16px;
  }
  .back-brand__mark { width: 26px; height: 26px; background: var(--green); }
  .back-brand__name { font-weight: 700; font-size: 60px; color: var(--white); letter-spacing: 3px; }

  .back-url {
    position: absolute; left: 0; right: 0; top: 330px; text-align: center;
    font-size: 17px; color: var(--white); letter-spacing: 4px;
  }
  .back-url strong { color: var(--green); font-weight: 700; }
</style>
</head>
<body>
  <section class="card card--front">
    <div class="brand">
      <span class="brand__mark"></span>
      <span class="brand__name">RIDGELINE</span>
    </div>

    <div class="divider"></div>

    <div class="person">
      <div class="person__name">DANIEL REYES</div>
      <div class="person__title">President</div>
    </div>

    <ul class="contacts">
      <li>
        <svg viewBox="0 0 24 24"><path d="M6.6 10.8a15.1 15.1 0 0 0 6.6 6.6l2.2-2.2c.3-.3.7-.4 1-.2 1.1.4 2.3.6 3.6.6.6 0 1 .4 1 1V20c0 .6-.4 1-1 1C10.6 21 3 13.4 3 4c0-.6.4-1 1-1h3.5c.6 0 1 .4 1 1 0 1.3.2 2.5.6 3.6.1.3 0 .7-.2 1z"/></svg>
        555-201-4870
      </li>
      <li>
        <svg viewBox="0 0 24 24"><path d="M7 1h10a2 2 0 0 1 2 2v18a2 2 0 0 1-2 2H7a2 2 0 0 1-2-2V3a2 2 0 0 1 2-2zm0 3v14h10V4zm5 15.5a1 1 0 1 0 0 2 1 1 0 0 0 0-2z"/></svg>
        555-318-9026
      </li>
      <li>
        <svg viewBox="0 0 24 24"><path d="M2 5h20v14H2zm2 2v1l8 5 8-5V7l-8 5z"/></svg>
        hello@ridgelinebuild.com
      </li>
    </ul>

    <div class="footer-band">
      <svg width="688" height="31" viewBox="0 0 688 31">
        <defs>
          <linearGradient id="band-green" x1="0" x2="1" y1="0" y2="0">
            <stop offset="0" stop-color="#7dc242"/>
            <stop offset="0.6" stop-color="#c4e59a"/>
            <stop offset="1" stop-color="#7dc242"/>
          </linearGradient>
        </defs>
        <rect x="0" y="0" width="440" height="15" fill="url(#band-green)"/>
        <path d="M0 18 H430 Q440 18 444 8 Q447 0 458 0 H688 V31 H0 Z" fill="#111111"/>
      </svg>
      <span class="footer-band__url">www.ridgelinebuild.com</span>
    </div>
  </section>

  <section class="card card--back">
    <div class="back-brand">
      <span class="back-brand__mark"></span>
      <span class="back-brand__name">RIDGELINE</span>
    </div>
    <div class="back-url">www.<strong>ridgelinebuild</strong>.com</div>
  </section>
</body>
</html>
```